BQR, LLC Original

I need a business card design for a new company in Gaithersburg, MD. Though the name of the company is Wiremasters Of Northfield (BQR) we specialize in commercial kitchen ventilation systems as a complete turnkey project or as a service provider. We can design the entire system including the hoods, fans, ductwork, and fire system. We also specialize in fire alarm service, design, install and inspection. We are experts on any Ventaro Dynamics equipment including Pulsar VXM, Pulsar Canopies, EMS controls, Standard controls, PCU filtration and Make-up Air units with heaters and cooling. We can repair/retrofit old water wash hood systems as well. We are experts with local code requirements and upgrades.

Industry/Entity Type

Business

Contact Information for Business Card

Dale Pruitt, Wiremasters Of Northfield, LLC; 240-555-0187 Cell, Larkfield, MD 20899. Dalep@wiremastersnorthfield.example

```html
<!DOCTYPE html>
<html lang="en">
<head>
<meta charset="utf-8">
<title>Of Northfield, LLC — Business Card</title>
<link rel="stylesheet" href="https://fonts.googleapis.com/css2?family=Arimo:wght@400&family=Tinos:wght@400&display=swap">
<style>
  :root {
    --yellow: #f2ee12;
    --black: #050505;
    --white: #f4fbfb;
    --backdrop: #3b3d42;
    --serif: "Tinos", "Times New Roman", serif;
    --sans: "Arimo", Arial, sans-serif;
  }
  html, body {
    margin: 0;
    padding: 0;
    width: 1200px;
    height: 960px;
    overflow: hidden;
    background: var(--backdrop);
  }
  .canvas {
    position: relative;
    width: 1200px;
    height: 960px;
  }
  .card {
    position: absolute;
    left: 250px;
    width: 700px;
    height: 400px;
    overflow: hidden;
    box-shadow: 0 10px 28px rgba(0,0,0,0.45);
  }
  .card-front { top: 50px; }
  .card-back { top: 510px; }
  .card-shapes {
    position: absolute;
    inset: 0;
    width: 100%;
    height: 100%;
  }
  .front-company {
    position: absolute;
    left: 0;
    right: 0;
    top: 140px;
    margin: 0;
    text-align: center;
    font-family: var(--serif);
    font-weight: 400;
    font-size: 68px;
    line-height: 1;
    color: var(--black);
    transform: rotate(-3deg);
  }
  .contact-name {
    position: absolute;
    left: 250px;
    top: 38px;
    margin: 0;
    font-family: var(--sans);
    font-size: 28px;
    line-height: 1;
    color: var(--black);
  }
  .contact-role {
    position: absolute;
    left: 290px;
    top: 72px;
    margin: 0;
    font-family: var(--sans);
    font-size: 18px;
    line-height: 1;
    color: var(--black);
  }
  .back-company {
    position: absolute;
    left: 0;
    right: 0;
    top: 188px;
    margin: 0;
    text-align: center;
    font-family: var(--serif);
    font-weight: 400;
    font-size: 40px;
    line-height: 1;
    color: var(--yellow);
  }
  .contact-list {
    position: absolute;
    left: 0;
    right: 0;
    top: 262px;
    margin: 0;
    padding: 0;
    list-style: none;
    text-align: center;
    font-family: var(--sans);
    font-size: 18px;
    line-height: 26px;
    color: var(--yellow);
  }
</style>
</head>
<body>
<main class="canvas">
  <section class="card card-front" aria-label="Business card front">
    <svg class="card-shapes" viewBox="0 0 700 400" preserveAspectRatio="none" aria-hidden="true">
      <rect width="700" height="400" fill="var(--black)"/>
      <polygon points="0,0 700,0 700,75 0,110" fill="var(--yellow)"/>
      <polygon points="0,110 700,75 700,220 0,290" fill="var(--white)"/>
    </svg>
    <h1 class="front-company">Of Northfield, LLC</h1>
  </section>

  <section class="card card-back" aria-label="Business card back">
    <svg class="card-shapes" viewBox="0 0 700 400" preserveAspectRatio="none" aria-hidden="true">
      <rect width="700" height="400" fill="var(--black)"/>
      <polygon points="0,0 700,0 700,70 0,150" fill="var(--yellow)"/>
    </svg>
    <p class="contact-name">Dale Pruitt</p>
    <p class="contact-role">Electricians</p>
    <h2 class="back-company">Of Northfield, LLC</h2>
    <ul class="contact-list">
      <li class="contact-phone">240-555-0187</li>
      <li class="contact-email">Dalep@wiremastersnorthfield.example</li>
      <li class="contact-address">Larkfield, MD 20899</li>
    </ul>
  </section>
</main>
</body>
</html>
```